Federal Government Proposal Development Consulting company needs a website designed and coded

I am looking for someone to design (using an existing logo, color palette, and text fonts) and code a wordpress-based website for a Proposal Development consulting company. I have full copy for all site pages and suggestions for images/ graphics and a few example design templates to go from.

One note, from a color perspective - I included a mockup of a business card to highlight a color scheme that I tend to like - if you look at the back of the business card, the blend of the grey, blue, with the neon green highlight as a separator really seems to pop. Just a thought as you are designing the page.

I would like to see 2-3 potential design layouts, and I will select one to move forward with. Then, I would like the site to be coded for WordPress (I can provide a login to my wordpress site). I would like 1 opportunity to review the coded site and make any final tweaks.

```html
<!DOCTYPE html>
<html lang="en">
<head>
<meta charset="utf-8">
<title>Clear Draft Consulting LLC</title>
<link rel="stylesheet" href="https://fonts.googleapis.com/css2?family=Gentium+Book+Plus:ital,wght@0,400;1,400&family=Montserrat:wght@400;500;600&display=swap">
<style>
:root{
  --navy:#0a2f8f;
  --blue:#0b3fa8;
  --deep:#062a78;
  --ink:#1b1b1b;
  --text:#333;
  --muted:#777;
  --grey:#e4e5e8;
  --line:#555;
  --white:#fff;
  --black:#050505;
}
*{box-sizing:border-box;margin:0;padding:0}
html,body{width:1200px;height:5245px;overflow:hidden;background:var(--white)}
body{position:relative;font-family:"Montserrat",sans-serif;color:var(--text)}
.abs{position:absolute}
.serif{font-family:"Gentium Book Plus",serif}
.btn{position:absolute;display:flex;align-items:center;justify-content:center;border-radius:22px;background:var(--navy);color:var(--white);font-family:"Gentium Book Plus",serif;font-size:17px}
.btn.light{background:var(--white);color:var(--ink)}
.heading{position:absolute;left:0;width:1200px;text-align:center;font-family:"Gentium Book Plus",serif;font-size:50px;color:var(--ink);line-height:1}

/* header */
.topbar{left:0;top:0;width:1200px;height:8px;background:var(--navy)}
.brand{left:108px;top:42px;display:flex;align-items:center;gap:12px}
.brand .name{font-family:"Gentium Book Plus",serif;font-size:34px;color:#555;line-height:1}
.brand .sub{font-family:"Gentium Book Plus",serif;font-size:16px;color:#555;margin-left:40px}
.brand .dot{width:30px;height:30px;border-radius:50%;background:var(--navy)}
.nav{left:524px;top:68px;display:flex;gap:28px;font-size:14px;font-weight:500;color:var(--ink)}

/* hero */
.hero{left:0;top:147px;width:1200px;height:628px;overflow:hidden}
.hero-photo{position:absolute;inset:0;background:linear-gradient(100deg,#3c3024 0%,#6b5846 35%,#a79a8b 60%,#d7d2cb 80%,#c2b8ab 100%)}
.hero h1{position:absolute;left:112px;top:160px;font-family:"Montserrat",sans-serif;font-weight:600;font-size:56px;color:var(--white);letter-spacing:1px}
.hero p{position:absolute;left:116px;top:240px;font-family:"Gentium Book Plus",serif;font-style:italic;font-size:19px;color:var(--white);line-height:27px}
.hero svg{position:absolute;left:0;bottom:0}

/* what we do */
.intro{left:112px;top:914px;width:976px;text-align:center;font-size:13.5px;line-height:30px;color:var(--text)}
.card{position:absolute;top:1141px;width:314px;height:362px;background:var(--white);box-shadow:0 2px 10px rgba(0,0,0,.12);border-bottom:4px solid var(--navy)}
.card .icon{position:absolute;left:22px;top:-12px;width:80px;height:80px;border-radius:50%;background:var(--white);box-shadow:0 2px 8px rgba(0,0,0,.15);display:flex;align-items:center;justify-content:center}
.card .icon i{width:34px;height:34px;background:var(--navy);border-radius:4px}
.card h3{position:absolute;left:24px;top:112px;font-size:17px;font-weight:500;color:var(--ink)}
.card p{position:absolute;left:24px;top:148px;width:266px;font-size:12.5px;line-height:22.5px;text-align:justify;color:var(--text)}
.card svg{position:absolute;right:22px;bottom:18px}

/* who we are */
.who{left:0;top:1593px;width:1200px;height:550px}
.who-panel{position:absolute;left:0;top:0;width:612px;height:550px;background:linear-gradient(135deg,#0a4fae 0%,#0a3f98 60%,#083684 100%)}
.who-photo{position:absolute;left:617px;top:0;width:583px;height:550px;background:linear-gradient(160deg,#0e2a4e 0%,#16507f 45%,#0b1f3a 100%)}
.who h2{position:absolute;left:102px;top:80px;font-family:"Gentium Book Plus",serif;font-size:52px;font-weight:400;color:var(--white)}
.who p{position:absolute;left:112px;top:152px;width:444px;font-size:13.5px;line-height:30.3px;color:var(--white)}

/* services */
.svc{position:absolute;width:200px;text-align:center}
.svc .ring{margin:0 auto;width:130px;height:130px;border-radius:50%;background:var(--white);box-shadow:0 2px 8px rgba(0,0,0,.15);border-left:5px solid var(--navy);border-bottom:5px solid var(--navy);display:flex;align-items:center;justify-content:center}
.svc .ring i{width:46px;height:46px;border-radius:6px;background:#1a1a1a}
.svc span{display:block;margin-top:28px;font-size:16px;font-weight:500;color:var(--ink)}
.vline{position:absolute;width:2px;height:110px;background:#8a8a8a}

/* expertise */
.sme{left:0;top:2903px;width:1200px;height:709px;background:radial-gradient(circle at 70% 40%,#1f5fd0 0%,#0b3fa8 45%,#072d80 100%)}
.sme .heading{color:var(--white);top:68px}
.tile{position:absolute;top:173px;width:314px;height:387px;background:var(--white)}
.tile .ph{position:absolute;left:12px;top:16px;width:290px;height:320px}
.tile span{position:absolute;left:0;bottom:14px;width:100%;text-align:center;font-size:16px;font-weight:500;color:var(--ink)}

/* contact */
.contact{left:0;top:3612px;width:1200px;height:688px;background:linear-gradient(180deg,#e9eaec,#dcdee2)}
.field{position:absolute;width:372px;border-bottom:1.5px solid var(--line);padding-bottom:14px}
.field b{display:block;font-size:13px;font-weight:500;color:var(--ink);margin-bottom:6px}
.field em{font-style:normal;font-size:12px;color:var(--muted)}
.field.focus{border-color:#3a8fd1}

/* testimonials */
.quote{position:absolute;top:4526px;width:440px}
.quote .av{position:absolute;left:0;top:0;width:80px;height:80px;border-radius:50%;background:linear-gradient(135deg,#6b4a33,#c9a27c)}
.quote h4{position:absolute;left:100px;top:12px;font-size:14px;font-weight:600;color:var(--ink)}
.quote .stars{position:absolute;left:100px;top:32px;font-size:10px;color:#e0a800;letter-spacing:1px}
.quote p{position:absolute;left:0;top:92px;width:440px;font-size:13.5px;line-height:29px;color:var(--text);text-align:justify}

/* footer */
.footer{left:0;top:4899px;width:1200px;height:346px;background:var(--black);color:var(--white)}
.footer .brand .name,.footer .brand .sub{color:var(--white)}
.footer .brand .dot{background:var(--white)}
.footer h5{position:absolute;font-size:15px;font-weight:600}
.links{position:absolute;left:560px;top:106px;font-family:"Gentium Book Plus",serif;font-size:13px;line-height:30.5px}
.cinfo{position:absolute;left:886px;display:flex;align-items:center;gap:18px;font-family:"Gentium Book Plus",serif;font-size:14px}
.cinfo i{width:20px;height:20px;border-radius:50%;background:var(--white);display:flex;align-items:center;justify-content:center}
.footer .rule{position:absolute;left:112px;top:289px;width:1088px;height:1px;background:#666}
.footer .copy{position:absolute;left:0;top:312px;width:1200px;text-align:center;font-size:12px}
</style>
</head>
<body>

<header>
  <div class="abs topbar"></div>
  <div class="abs brand">
    <div>
      <div class="name">Clear Draft</div>
      <div class="sub">Consulting LLC</div>
    </div>
    <div class="dot"></div>
  </div>
  <nav class="abs nav"><span>Home</span><span>Work with Us</span><span>Work for Us</span><span>About Us</span></nav>
  <div class="btn" style="left:965px;top:57px;width:121px;height:40px;font-size:17px">Contact</div>
</header>

<section class="abs hero">
  <div class="hero-photo" role="img" aria-label="Young man with glasses working on a laptop in a café"></div>
  <h1>Generate Success</h1>
  <p>Fuel Innovation in Proposal Excellence with Clear Draft!<br>Click here to explore our services.</p>
  <div class="btn" style="left:116px;top:317px;width:143px;height:37px">Get Started</div>
  <svg width="1200" height="160" viewBox="0 0 1200 160">
    <path d="M0 30 C300 110 700 140 1200 40 L1200 160 L0 160 Z" fill="#fff"/>
    <path d="M300 112 C600 150 950 140 1200 40 C980 150 620 170 300 112 Z" fill="#0a2f8f"/>
  </svg>
</section>

<section>
  <h2 class="heading" style="top:852px">What We Do</h2>
  <p class="abs intro">Clear Draft, specializes in advancing an organization through a comprehensive suite of services designed to modernize the proposal development process. From innovative Capture Management strategies that pinpoint lucrative opportunities, meticulous Proposal Development services that transform concepts into effective narratives, and cutting-edge Generative AI techniques that create domain-aware content accelerating proposal draft development, we are your dedicated partner in securing success. With a unique fusion of technical expertise and exceptional writing capabilities, we surpass industry standards and set new benchmarks for excellence.</p>

  <article class="card" style="left:108px">
    <div class="icon"><i></i></div>
    <h3>Capture Management</h3>
    <p>Elevate your business development strategy with our Capture Management services. From opportunity identification to strategic planning, our experts will guide you through a meticulous process, ensuring the pursuit of the right contracts to position your organization for success.</p>
    <svg width="20" height="14" viewBox="0 0 20 14"><path d="M1 7H18M12 1l6 6-6 6" stroke="#111" stroke-width="1.8" fill="none"/></svg>
  </article>
  <article class="card" style="left:448px">
    <div class="icon"><i></i></div>
    <h3>Proposal Development</h3>
    <p>Transform your vision into winning proposals with our Proposal Development services. We specialize in persuasive narratives, clear technical solutions, and strategic pricing models. From meticulous compliance reviews to captivating executive summaries.</p>
    <svg width="20" height="14" viewBox="0 0 20 14"><path d="M1 7H18M12 1l6 6-6 6" stroke="#111" stroke-width="1.8" fill="none"/></svg>
  </article>
  <article class="card" style="left:786px">
    <div class="icon"><i></i></div>
    <h3>Generative AI</h3>
    <p>Revolutionize your proposal writing process with our domain-aware Generative AI services. Using customer-installed tools, we leverage domain-aware artificial intelligence to generate innovative and tailored proposal content.</p>
    <svg width="20" height="14" viewBox="0 0 20 14"><path d="M1 7H18M12 1l6 6-6 6" stroke="#111" stroke-width="1.8" fill="none"/></svg>
  </article>
</section>

<section class="abs who">
  <div class="who-panel"></div>
  <div class="who-photo" role="img" aria-label="Two colleagues reviewing a tablet beside a server room"></div>
  <h2>Who We Are</h2>
  <p>Lorem ipsum dolor sit amet, consectetur adipiscing elit, sed do eiusmod tempor incididunt ut labore et dolore magna aliqua. Ut enim ad minim veniam, quis nostrud exercitation ullamco laboris nisi ut aliquip ex ea commodo consequat. Duis aute irure dolor in reprehenderit in voluptate velit esse cillum dolore eu fugiat nulla pariatur. Excepteur sint occaecat cupidatat non proident, sunt in culpa qui officia deserunt mollit anim id est laborum</p>
  <div class="btn light" style="left:108px;top:413px;width:147px;height:37px">Read More</div>
</section>

<section>
  <h2 class="heading" style="top:2215px">Our Services</h2>
  <div class="svc" style="left:124px;top:2318px"><div class="ring"><i></i></div><span>Generative AI</span></div>
  <div class="svc" style="left:371px;top:2318px"><div class="ring"><i></i></div><span>Technical Solutioning</span></div>
  <div class="svc" style="left:619px;top:2318px"><div class="ring"><i></i></div><span>Technical Writer</span></div>
  <div class="svc" style="left:868px;top:2318px"><div class="ring"><i></i></div><span>Generative AI</span></div>
  <div class="vline" style="left:344px;top:2343px"></div>
  <div class="vline" style="left:601px;top:2343px"></div>
  <div class="vline" style="left:849px;top:2343px"></div>

  <div class="svc" style="left:124px;top:2551px"><div class="ring"><i></i></div><span>Price to Win</span></div>
  <div class="svc" style="left:371px;top:2551px"><div class="ring"><i></i></div><span>Volume Lead</span></div>
  <div class="svc" style="left:619px;top:2551px"><div class="ring"><i></i></div><span>Development</span></div>
  <div class="svc" style="left:868px;top:2551px"><div class="ring"><i></i></div><span>Book Boss</span></div>
  <div class="vline" style="left:344px;top:2576px"></div>
  <div class="vline" style="left:601px;top:2576px"></div>
  <div class="vline" style="left:849px;top:2576px"></div>

  <div class="btn" style="left:528px;top:2778px;width:144px;height:37px">View All</div>
</section>

<section class="abs sme">
  <h2 class="heading">Subject Matter Expertise</h2>
  <div class="tile" style="left:110px"><div class="ph" role="img" aria-label="Glowing circuit network" style="background:linear-gradient(180deg,#0c3c8a,#2a6fd1 45%,#c68a2c 75%,#1a1a2e)"></div><span>Generative AI</span></div>
  <div class="tile" style="left:442px"><div class="ph" role="img" aria-label="Engineer working at computer screens" style="background:linear-gradient(160deg,#0e2e4a,#1f5b7e 45%,#0a1320)"></div><span>Software&nbsp; Engineering</span></div>
  <div class="tile" style="left:772px"><div class="ph" role="img" aria-label="Hands on a keyboard with a security lock" style="background:linear-gradient(160deg,#2a6fe0,#0d3fa8 55%,#0a2468)"></div><span>Cybersecurity</span></div>
  <div class="btn light" style="left:528px;top:599px;width:144px;height:38px">View All</div>
</section>

<section class="abs contact">
  <h2 class="heading" style="top:88px">Contact Us</h2>
  <div class="field focus" style="left:204px;top:203px"><b>Name</b><em>First Name</em></div>
  <div class="field" style="left:623px;top:203px"><b>Email Address</b><em>@lorem.com</em></div>
  <div class="field" style="left:204px;top:323px"><b>Phone</b><em>123 - 456 - 7890</em></div>
  <div class="field" style="left:623px;top:323px"><b>Subject</b><em>New Project</em></div>
  <div class="field" style="left:202px;top:435px;width:793px;height:127px"><b>Message</b><em>Lorem ipsum dolor sit</em></div>
  <div class="btn" style="left:513px;top:603px;width:163px;height:40px">Send Message</div>
</section>

<section>
  <h2 class="heading" style="top:4380px">Testimonials</h2>
  <div class="quote" style="left:119px">
    <div class="av" role="img" aria-label="Portrait of Andrew"></div>
    <h4>ANDREW</h4><div class="stars">★★★★★</div>
    <p>Lorem ipsum dolor sit amet, consectetur adipiscing elit, sed do eiusmod tempor incididunt ut labore et dolore magna aliqua. Ut enim ad minim veniam, quis nostrud exercitation ullamco laboris nisi ut aliquip ex ea commodo consequat.</p>
  </div>
  <div class="abs" style="left:578px;top:4604px;width:2px;height:112px;background:#999"></div>
  <div class="quote" style="left:627px">
    <div class="av" role="img" aria-label="Portrait of Diana" style="background:linear-gradient(135deg,#3a2218,#a8735a)"></div>
    <h4>DIANA</h4><div class="stars">★★★★★</div>
    <p>Lorem ipsum dolor sit amet, consectetur adipiscing elit, sed do eiusmod tempor incididunt ut labore et dolore magna aliqua. Ut enim ad minim veniam, quis nostrud exercitation ullamco laboris nisi ut aliquip ex ea commodo consequat.</p>
  </div>
  <div class="btn" style="left:536px;top:4771px;width:128px;height:43px">View All</div>
</section>

<footer class="abs footer">
  <div class="abs brand" style="left:112px;top:82px">
    <div>
      <div class="name">Clear Draft</div>
      <div class="sub">Consulting LLC</div>
    </div>
    <div class="dot"></div>
  </div>
  <h5 style="left:560px;top:76px">Quick Links</h5>
  <div class="links">Home<br>Work with Us<br>Work for Us<br>About Us<br>Contact</div>
  <h5 style="left:886px;top:76px">Contact Details</h5>
  <div class="cinfo" style="top:112px"><i><svg width="11" height="11" viewBox="0 0 24 24"><path d="M6.6 10.8a15 15 0 006.6 6.6l2.2-2.2c.3-.3.7-.4 1-.2 1.1.4 2.3.6 3.6.6.6 0 1 .4 1 1V20c0 .6-.4 1-1 1A17 17 0 013 4c0-.6.4-1 1-1h3.5c.6 0 1 .4 1 1 0 1.3.2 2.5.6 3.6.1.3 0 .7-.2 1z" fill="#000"/></svg></i>(410) 555-0142</div>
  <div class="cinfo" style="top:155px"><i><svg width="11" height="9" viewBox="0 0 22 16"><rect x="1" y="1" width="20" height="14" fill="none" stroke="#000" stroke-width="2"/><path d="M1 1l10 8 10-8" fill="none" stroke="#000" stroke-width="2"/></svg></i>info@cleardraftco.com</div>
  <div class="rule"></div>
  <div class="copy">Copyright © &nbsp;2023 &nbsp;Clear Draft . All rights reserved.</div>
</footer>

</body>
</html>
```